KRL Stationery Design Project

Dear Designers,
We need a new stationery design for company to match our new logo.
Designers should provide a design for the following:
1. Business Card: 3.5x2 Inches.
2. Letterhead: A4 size.
3. Envelops: 25x35.5 Cm.
You can keep the Arabic name at the bottom of the logo Or you can use the separate attached Arabic Name.
Please refer to the attached logo guide for design information.
Sample Business Card information:
Name: Tarek Sowan
Position: Operation Manager
Tel: +966 920007164 Ex. 500
Fax: +966 (3)8842617
Mob: +966 (5)00263817
email: tarek@krl-example.com.sa
URL: www.krl-example.com.sa
Address:
Nakheel Heights, Suite 718
Zayed bin Omar Str.
Khobar, 31847
Saudi Arabia
Updates
Dear All,
Please note, we had uploaded our logo along with Arabic writing in Adobe illustrator format (.ai).
Regards,
Karim
Dear All,
A sample data for the business card had been added as per your request.
Regards,
Karim

```html
<!DOCTYPE html>
<html lang="en">
<head>
<meta charset="utf-8">
<title>KRL Business Card</title>
<link rel="stylesheet" href="https://fonts.googleapis.com/css2?family=Open+Sans:wght@400;700;800&display=swap">
<style>
  :root {
    --stage: #1e1e1f;
    --card: #ffffff;
    --navy: #0e2b4f;
    --ink: #3a3a3a;
    --rule: #a9a9a9;
  }
  * { margin: 0; padding: 0; box-sizing: border-box; }
  html, body { width: 960px; height: 1200px; overflow: hidden; }
  body {
    background: var(--stage);
    font-family: "Open Sans", Arial, sans-serif;
    color: var(--ink);
    position: relative;
  }
  .card {
    position: absolute;
    left: 60px;
    width: 840px;
    height: 478px;
    background: var(--card);
    border-radius: 40px;
    box-shadow: 0 6px 18px rgba(0,0,0,.45);
  }
  .card--front { top: 82px; }
  .card--back  { top: 643px; }

  .brand {
    position: absolute;
    display: flex;
    align-items: center;
    gap: 22px;
    font-weight: 800;
    color: var(--navy);
    letter-spacing: 2px;
    line-height: 1;
  }
  .brand__mark {
    width: 34px; height: 34px;
    border-radius: 50%;
    background: var(--navy);
  }
  .card--front .brand { left: 52px; top: 70px; font-size: 120px; }
  .card--back .brand { left: 50%; top: 50%; transform: translate(-50%, -50%); font-size: 130px; }

  .holder { position: absolute; left: 28px; top: 308px; }
  .holder__name { font-size: 25px; color: #3c3c3c; }
  .holder__role { font-size: 18px; color: #4a4a4a; margin-top: 2px; }

  .divider {
    position: absolute;
    left: 28px; right: 36px; top: 380px;
    border-top: 2px solid var(--rule);
  }

  .contact {
    position: absolute;
    top: 398px;
    font-size: 19px;
    line-height: 28px;
    color: #3a3a3a;
  }
  .contact li { list-style: none; display: flex; align-items: center; gap: 6px; }
  .contact svg { width: 15px; height: 15px; fill: #333; flex: none; }
  .contact--phones { left: 28px; }
  .contact--web { left: 238px; }
  .contact--address { right: 36px; text-align: right; }
  .contact--address li { justify-content: flex-end; }
</style>
</head>
<body>

<section class="card card--front">
  <div class="brand"><span>KRL</span><span class="brand__mark"></span></div>

  <div class="holder">
    <p class="holder__name">Your Name</p>
    <p class="holder__role">Designation</p>
  </div>

  <div class="divider"></div>

  <ul class="contact contact--phones">
    <li>
      <svg viewBox="0 0 16 16" aria-hidden="true"><path d="M1 5c0-2 3-3 7-3s7 1 7 3v1h-3V5H4v1H1zM3 8l2-2h6l2 2v6H3z"/></svg>
      123-123-1234
    </li>
    <li>
      <svg viewBox="0 0 16 16" aria-hidden="true"><path d="M4 2h8v4H4zM1 7h14v6h-3v-2H4v2H1zM5 12h6v2H5z"/></svg>
      123-123-1234
    </li>
  </ul>

  <ul class="contact contact--web">
    <li>
      <svg viewBox="0 0 16 16" aria-hidden="true"><path d="M8 1a7 7 0 1 0 4 12.7l-.9-1.3A5.4 5.4 0 1 1 13.4 8v.8c0 .8-.5 1.2-1 1.2s-1-.4-1-1.2V5h-1.5v.6A3.4 3.4 0 1 0 10 11a2.5 2.5 0 0 0 4.9-2.2V8A7 7 0 0 0 8 1zm0 9.2a2.2 2.2 0 1 1 0-4.4 2.2 2.2 0 0 1 0 4.4z"/></svg>
      info@krl-example.com.sa
    </li>
    <li>
      <svg viewBox="0 0 16 16" aria-hidden="true"><circle cx="8" cy="8" r="7"/></svg>
      www.krl-example.com.sa
    </li>
  </ul>

  <ul class="contact contact--address">
    <li>1234, Suite# 123, Street Name</li>
    <li>State NAME, Country Code</li>
  </ul>
</section>

<section class="card card--back">
  <div class="brand"><span>KRL</span><span class="brand__mark"></span></div>
</section>

</body>
</html>
```